Buch-/eBook-Cover für Sachbuch gesucht
Zielgruppe
We're selfpublishing nonfiction books. Interested are adults - mostly man (age range: 25-50) - who want to learn more about leadership at their workplaces.
Aufgabenstellung
The design should be clean and simple, title easy to read, good color contrast (the cover has to stand out from an white background).

```html
<!DOCTYPE html>
<html lang="en">
<head>
<meta charset="utf-8">
<title>Leadership – Book Cover</title>
<link href="https://fonts.googleapis.com/css2?family=Bebas+Neue&family=Raleway:wght@800&display=swap" rel="stylesheet">
<style>
  :root {
    --backdrop: #333333;
    --cover-cream: #ffffcc;
    --accent-red: #990000;
    --ink-dark: #333333;
    --author-white: #ffffff;
  }
  html, body {
    margin: 0;
    padding: 0;
    overflow: hidden;
    background: var(--backdrop);
  }
  .canvas {
    width: 1075px;
    height: 1200px;
    display: block;
  }
  .cover-sheet { fill: var(--cover-cream); }
  .accent-band { fill: var(--accent-red); }
  .title-main {
    font-family: "Bebas Neue", "Oswald", sans-serif;
    font-size: 112px;
    fill: var(--accent-red);
  }
  .subtitle {
    font-family: "Bebas Neue", "Oswald", sans-serif;
    font-size: 74px;
    fill: var(--ink-dark);
  }
  .subtitle--small { font-size: 53px; }
  .author-name {
    font-family: "Raleway", "Arial", sans-serif;
    font-weight: 800;
    font-size: 24px;
    fill: var(--author-white);
  }
</style>
</head>
<body>
<svg class="canvas" viewBox="0 0 1075 1200" xmlns="http://www.w3.org/2000/svg">
  <rect class="cover-sheet" x="217" y="147" width="641" height="906"/>

  <g class="title-block">
    <rect class="accent-band" x="217" y="288" width="70" height="109"/>
    <rect class="accent-band" x="788" y="288" width="70" height="109"/>
    <text class="title-main" x="537" y="382" text-anchor="middle">LEADERSHIP</text>
  </g>

  <g class="subtitle-block" text-anchor="middle">
    <text class="subtitle" x="537" y="511">FOSTERING</text>
    <text class="subtitle" x="537" y="593">GROWTH</text>
    <text class="subtitle subtitle--small" x="537" y="661">AND</text>
    <text class="subtitle" x="537" y="741">INSPIRING</text>
    <text class="subtitle" x="537" y="822">EXCELLENCE</text>
  </g>

  <g class="author-block">
    <rect class="accent-band" x="217" y="924" width="641" height="54"/>
    <text class="author-name" x="537" y="961" text-anchor="middle">Daniel Harker</text>
  </g>
</svg>
</body>
</html>
```